Flat Belly Design Graphics for Social

I want to create 9 social media graphics (new Instagram size 4:5 (1080 x 1350 pixels) focusing on our Flat Belly Graphics, using the pics attached. Use the attached pics, NO RANDOM STOCK PHOTOGRAPHY. For the color scheme of the graphics, the color palette is attached. YOU MUST POST ALL 9 GRAPHICS IN ONE ENTRY.
Using the 3 titles below, create one set of graphics. 1) with all text, then for the others, use the pictures as detailed below in IMPORTANT:
1. Ten-Week Bright Morning Reboot
2. The Quick Garden Kitchen Menu Guide
3. Studio Habits for Lasting Energy Past Midlife - Zero Gym Needed
IMPORTANT:
Only use RK Pic 1 and RK Pic 2 with the title, Ten-Week Bright Morning Reboot
Only use meal plan1 and meal plan2 pics with the title, Quick Garden Kitchen Menu Guide
Only use studio habits 1 and studio habits 2 pics with the title, Studio Habits for Lasting Energy Past Midlife - Zero Gym Needed
women over 40

```html
<!DOCTYPE html>
<html lang="en">
<head>
<meta charset="utf-8">
<title>Social Graphics Set</title>
<link href="https://fonts.googleapis.com/css2?family=Anton&family=Oswald:wght@300;400;500;600&family=Kaushan+Script&display=swap" rel="stylesheet">
<style>
:root{
  --stage:#9a9a9a;
  --green:#2f4a45;
  --pink:#e6a3b8;
  --blush:#f4d3de;
  --blush-light:#fbecf1;
  --ink-light:#fbe9ef;
  --photo-skin:#c9a58e;
  --photo-food:#8a5a3c;
}
*{margin:0;padding:0;box-sizing:border-box}
html,body{width:1200px;height:853px;overflow:hidden;background:var(--stage)}
.set{position:relative;width:1200px;height:853px}
.card{position:absolute;overflow:hidden;background:linear-gradient(180deg,var(--blush-light),var(--blush));color:var(--green);font-family:"Oswald",sans-serif}
.card--hero{left:76px;top:189px;width:391px;height:488px;background:radial-gradient(circle at 50% 55%,#fff3f7 0%,var(--blush) 70%,#eeb9c9 100%)}
.card--sm{width:186px;height:233px}
.c1{left:550px}.c2{left:753px}.c3{left:959px}
.r1{top:55px}.r2{top:310px}.r3{top:562px}
.card--green{background:var(--green);color:var(--ink-light)}
.abs{position:absolute;z-index:2}
.heavy{font-family:"Anton",sans-serif;text-transform:uppercase;line-height:1}
.light{font-family:"Oswald",sans-serif;font-weight:400;text-transform:uppercase;line-height:1}
.tag{display:inline-block;background:var(--green);color:var(--ink-light);font-family:"Oswald",sans-serif;font-weight:300;text-transform:uppercase;line-height:.95;padding:2px 4px}
.tag--outline{background:var(--green);border:1px solid var(--ink-light)}
.photo{position:absolute;z-index:1}
.photo--people{background:linear-gradient(180deg,rgba(201,165,142,0) 0%,var(--photo-skin) 30%,#a98b7f 70%,#5d7191 100%)}
.photo--coach{background:linear-gradient(180deg,rgba(0,0,0,0) 0%,#b58c76 25%,#efeae6 50%,#1f1f24 85%)}
.photo--food{background:linear-gradient(135deg,#c8463c 0%,var(--photo-food) 45%,#6f9a3a 100%)}
.dot{position:absolute;z-index:2;border-radius:50%;background:var(--green)}
.dot--pink{background:var(--pink)}
svg{position:absolute;z-index:0}
</style>
</head>
<body>
<main class="set">

  <!-- Hero: studio habits -->
  <section class="card card--hero">
    <p class="abs light" style="left:0;right:0;top:28px;text-align:center;font-size:41px;font-weight:500">Studio Habits</p>
    <p class="abs light" style="left:0;right:0;top:73px;text-align:center;font-size:34px">For Lasting Energy</p>
    <div class="abs" style="left:40px;top:115px;display:flex;align-items:center;gap:8px">
      <span class="heavy" style="font-size:44px">Past Midlife</span>
      <span class="tag" style="font-size:18px">Zero Gym<br>Needed</span>
    </div>
    <div class="photo photo--people" role="img" aria-label="Two women sharing a secret, one whispering and one smiling in surprise" style="left:85px;top:185px;width:225px;height:303px"></div>
    <span class="dot" style="left:52px;top:222px;width:16px;height:16px"></span>
    <span class="dot" style="left:75px;top:230px;width:26px;height:26px"></span>
    <span class="dot" style="left:298px;top:392px;width:30px;height:30px"></span>
    <span class="dot" style="left:333px;top:384px;width:16px;height:16px"></span>
  </section>

  <!-- Row 1: morning reboot -->
  <section class="card card--sm c1 r1">
    <svg width="186" height="233" viewBox="0 0 186 233" aria-hidden="true"><path d="M0 58 C40 50 60 80 45 110 C30 150 110 150 115 200 L120 233 L0 233Z" fill="var(--pink)" opacity=".8"/><path d="M0 58 C40 50 60 80 45 110 C30 150 110 150 115 200 L120 233" fill="none" stroke="var(--green)" stroke-width="4"/></svg>
    <p class="abs heavy" style="right:14px;top:14px;font-size:36px">Ten-Week</p>
    <p class="abs heavy" style="right:14px;top:56px;font-size:16px">Bright Morning</p>
    <div class="photo photo--coach" role="img" aria-label="Smiling woman in a white cropped sweater presenting her waist" style="left:30px;top:80px;width:100px;height:153px"></div>
    <div class="abs" style="left:126px;top:82px;width:54px;height:54px;border-radius:50%;background:var(--green);border:3px solid var(--pink);display:flex;align-items:center;justify-content:center"><span class="heavy" style="color:var(--ink-light);font-size:12px">Reboot</span></div>
    <span class="dot" style="left:136px;top:142px;width:16px;height:16px"></span>
    <span class="dot" style="left:156px;top:157px;width:7px;height:7px"></span>
  </section>

  <section class="card card--sm card--green c2 r1">
    <p class="abs heavy" style="left:12px;top:14px;font-size:28px;line-height:1.05">Ten-Week<br>Bright</p>
    <p class="abs light" style="left:12px;top:80px;font-size:22px;font-weight:300;line-height:1.1">Morning<br>Reboot</p>
    <div class="photo photo--coach" role="img" aria-label="Smiling woman in a white cropped sweater presenting her waist" style="left:92px;top:80px;width:94px;height:153px"></div>
    <span class="dot dot--pink" style="left:60px;top:195px;width:16px;height:16px"></span>
    <span class="dot dot--pink" style="left:63px;top:183px;width:7px;height:7px"></span>
    <span class="dot" style="left:150px;top:105px;width:16px;height:16px;background:#1e302c"></span>
  </section>

  <section class="card card--sm card--green c3 r1">
    <svg width="186" height="233" viewBox="0 0 186 233" aria-hidden="true"><path d="M0 0 H186 V20 C150 40 150 110 120 100 C90 90 80 115 40 110 C20 108 10 112 0 115Z" fill="var(--blush)"/><circle cx="160" cy="55" r="8" fill="var(--pink)"/><circle cx="150" cy="72" r="5" fill="var(--pink)"/></svg>
    <p class="abs heavy" style="left:14px;top:14px;font-size:36px;color:var(--green)">Ten-Week</p>
    <p class="abs heavy" style="left:14px;top:56px;font-size:17px;color:var(--green);line-height:1.1">Bright<br>Morning</p>
    <span class="abs tag tag--outline" style="left:18px;top:124px;font-size:15px;padding:4px 5px">Reboot</span>
    <div class="photo photo--coach" role="img" aria-label="Smiling woman in a white cropped sweater presenting her waist" style="left:84px;top:80px;width:102px;height:153px"></div>
  </section>

  <!-- Row 2: garden kitchen menu -->
  <section class="card card--sm c1 r2">
    <svg width="186" height="233" viewBox="0 0 186 233" aria-hidden="true"><path d="M0 0 H186 V108 C150 100 120 130 80 125 C40 120 30 138 0 138Z" fill="var(--green)"/><circle cx="34" cy="150" r="9" fill="var(--pink)"/><circle cx="37" cy="168" r="4" fill="var(--pink)"/></svg>
    <p class="abs heavy" style="right:14px;top:14px;font-size:26px;color:var(--ink-light)">The Quick</p>
    <p class="abs heavy" style="right:14px;top:46px;font-size:24px;color:var(--ink-light)">Garden Kitchen</p>
    <span class="abs tag" style="left:18px;top:90px;font-size:15px;background:var(--ink-light);color:var(--green)">Menu Guide</span>
    <div class="photo photo--food" role="img" aria-label="Bowls of berries, grapes and grains on a wooden table" style="left:67px;top:102px;width:150px;height:150px;border-radius:50%;border:3px solid #fff"></div>
  </section>

  <section class="card card--sm c2 r2">
    <p class="abs heavy" style="left:14px;top:14px;font-size:26px">The Quick</p>
    <div class="abs" style="left:14px;top:46px;display:flex;gap:6px;align-items:flex-start">
      <span class="heavy" style="font-size:19px;line-height:1.1">Garden<br>Kitchen</span>
      <span class="tag" style="font-size:17px">Menu<br>Guide</span>
    </div>
    <span class="dot" style="left:56px;top:94px;width:13px;height:13px"></span>
    <span class="dot" style="left:47px;top:99px;width:6px;height:6px"></span>
    <div class="photo photo--food" role="img" aria-label="Meal plan sheet among chicken, asparagus, potatoes and grains" style="left:0;top:108px;width:186px;height:125px;background:linear-gradient(180deg,rgba(138,90,60,0) 0%,var(--photo-food) 30%,#6f7e3a 100%)"></div>
  </section>

  <section class="card card--sm card--green c3 r2">
    <div class="photo photo--food" role="img" aria-label="Notebook meal plan framed by fresh vegetables, fruit and salmon" style="left:0;top:0;width:186px;height:124px"></div>
    <div class="abs" style="left:0;top:124px;width:186px;height:30px;background:var(--blush);z-index:1"></div>
    <p class="abs heavy" style="left:0;right:0;top:128px;text-align:center;font-size:24px;color:var(--green)">The Quick</p>
    <p class="abs" style="left:0;right:0;top:155px;text-align:center;font-family:'Kaushan Script',cursive;font-size:21px;color:var(--ink-light)">Garden Kitchen</p>
    <span class="dot dot--pink" style="left:40px;top:198px;width:12px;height:12px"></span>
    <span class="dot dot--pink" style="left:32px;top:200px;width:5px;height:5px"></span>
    <p class="abs light" style="left:66px;top:193px;font-size:22px">Menu Guide</p>
  </section>

  <!-- Row 3: studio habits -->
  <section class="card card--sm c1 r3">
    <svg width="186" height="233" viewBox="0 0 186 233" aria-hidden="true"><path d="M186 40 C150 55 150 120 130 160 C115 190 120 215 110 233 H186Z" fill="var(--pink)"/><path d="M186 40 C150 55 150 120 130 160" fill="none" stroke="var(--green)" stroke-width="4"/></svg>
    <p class="abs heavy" style="left:16px;top:14px;font-size:21px">Studio Habits</p>
    <p class="abs heavy" style="left:16px;top:38px;font-size:15px">For Lasting Energy</p>
    <p class="abs heavy" style="left:16px;top:58px;font-size:20px">Past Midlife</p>
    <span class="abs tag" style="left:16px;top:88px;font-size:15px">Zero Gym<br>Needed</span>
    <span class="dot" style="left:66px;top:129px;width:14px;height:14px"></span>
    <span class="dot" style="left:58px;top:135px;width:6px;height:6px"></span>
    <div class="photo photo--people" role="img" aria-label="Two women sharing a secret, one whispering and one smiling in surprise" style="left:74px;top:92px;width:112px;height:141px"></div>
  </section>

  <section class="card card--sm c2 r3">
    <div class="photo photo--people" role="img" aria-label="Two women sharing a secret, one whispering and one smiling in surprise" style="left:0;top:0;width:186px;height:125px;background:linear-gradient(180deg,#5a4037 0%,var(--photo-skin) 50%,rgba(201,165,142,0) 100%)"></div>
    <p class="abs heavy" style="left:15px;top:145px;font-size:21px">Studio Habits</p>
    <p class="abs heavy" style="left:15px;top:169px;font-size:17px">For Lasting Energy</p>
    <span class="dot" style="left:150px;top:172px;width:12px;height:12px"></span>
    <span class="dot" style="left:166px;top:177px;width:6px;height:6px"></span>
    <div class="abs" style="left:15px;top:192px;display:flex;gap:6px;align-items:center">
      <span class="heavy" style="font-size:20px">Past Midlife</span>
      <span class="tag" style="font-size:9px">Zero Gym<br>Needed</span>
    </div>
  </section>

  <section class="card card--sm c3 r3" style="background:radial-gradient(circle at 50% 55%,#fff3f7 0%,var(--blush) 70%,#eeb9c9 100%)">
    <p class="abs light" style="left:0;right:0;top:14px;text-align:center;font-size:20px;font-weight:500">Studio Habits</p>
    <p class="abs light" style="left:0;right:0;top:36px;text-align:center;font-size:16px">For Lasting Energy</p>
    <div class="abs" style="left:22px;top:56px;display:flex;gap:5px;align-items:center">
      <span class="heavy" style="font-size:21px">Past Midlife</span>
      <span class="tag" style="font-size:9px">Zero Gym<br>Needed</span>
    </div>
    <div class="photo photo--people" role="img" aria-label="Two women sharing a secret, one whispering and one smiling in surprise" style="left:38px;top:92px;width:112px;height:141px"></div>
    <span class="dot" style="left:26px;top:105px;width:7px;height:7px"></span>
    <span class="dot" style="left:35px;top:110px;width:13px;height:13px"></span>
    <span class="dot" style="left:150px;top:190px;width:14px;height:14px"></span>
    <span class="dot" style="left:166px;top:184px;width:7px;height:7px"></span>
  </section>

</main>
</body>
</html>
```